Business Card Design For Office Furniture Clearance Company

Kestrel Office Clearance - our company name pretty much explains what we do, we clear offices for high end clients, mainly plc's and large international companies.

We require a nice looking business card that displays professionalism but without being too serious.

It would be nice to see just a little more than a conventional boring business card, make sure you add some flare.

Industry/Entity Type

Office Furniture

Contact Information for Business Card

CARD 1

Mark Holloway
Director
mark@kestrelofficeclearance.co.uk
m: 07700 153928

t: 01632 960418
www.kestrelofficeclearance.co.uk

Kestrel Office Clearance
Unit K4 B
2-8 Fenwick Lane
Ashcombe
Northvale
ZZ9 4QT

tidy offices, zero fuss… we handle every last desk.

CARD 2

Peter Radford
Director
peter@kestrelofficeclearance.co.uk
m: 07700 382615

t: 01632 960418

Kestrel Office Clearance
Unit K4 B
2-8 Fenwick Lane
Ashcombe
Northvale
ZZ9 4QT

Font styles to use
Sans Serif

Requirements
Must have
• A white background - as we have a blue logo.
Nice to have
• Nice use of the logo - play around with this and dissect it.

```html
<!DOCTYPE html>
<html lang="en">
<head>
<meta charset="utf-8">
<title>Kestrel Office Clearance – Business Card</title>
<link rel="stylesheet" href="https://fonts.googleapis.com/css2?family=Open+Sans:wght@400;600;700&family=Oswald:wght@400&display=swap">
<style>
  :root {
    --brand-blue: #0a7bc1;
    --card-clear: #f6f8fa;
    --card-edge: #d9dee3;
    --page-bg: #e8ebee;
    --ink-white: #ffffff;
  }
  * { margin: 0; padding: 0; box-sizing: border-box; }
  html, body {
    width: 1200px; height: 900px; overflow: hidden;
    background: var(--page-bg);
    font-family: "Open Sans", Arial, sans-serif;
  }
  .canvas { position: relative; width: 1200px; height: 900px; }

  .card {
    position: absolute;
    display: flex;
    width: 556px; height: 343px;
    box-shadow: 0 6px 18px rgba(0,0,0,0.12);
  }
  .card--front { left: 238px; top: 62px; }
  .card--back  { left: 457px; top: 518px; width: 560px; }

  .card__panel { height: 100%; }
  .card__panel--blue { background: var(--brand-blue); color: var(--ink-white); }
  .card__panel--clear {
    background: var(--card-clear);
    border: 1px solid var(--card-edge);
    display: flex; align-items: center; justify-content: center;
  }
  .card--front .card__panel--blue { width: 277px; padding: 56px 0 0 24px; }
  .card--front .card__panel--clear { width: 279px; border-left: none; }
  .card--back .card__panel--clear { width: 281px; border-right: none; }
  .card--back .card__panel--blue {
    width: 279px;
    display: flex; flex-direction: column; justify-content: center; align-items: center;
    padding-bottom: 18px;
  }

  .person__name { font-size: 18px; font-weight: 600; line-height: 22px; }
  .person__role { font-size: 14px; line-height: 18px; }
  .company { margin-top: 20px; }
  .company__name { font-size: 16px; font-weight: 700; line-height: 22px; }
  .company__address { font-size: 14.5px; line-height: 21px; }

  .contacts { list-style: none; margin-top: 20px; }
  .contacts__item {
    display: flex; align-items: center; gap: 9px;
    font-size: 14px; line-height: 20.5px;
  }
  .contacts__icon { width: 12px; height: 12px; flex: none; fill: var(--ink-white); }

  .brand-mark { display: flex; flex-direction: column; align-items: center; gap: 12px; }
  .brand-mark__dot {
    width: 110px; height: 110px; border-radius: 50%;
    background: var(--brand-blue);
  }
  .brand-mark__name {
    font-size: 17px; font-weight: 700; line-height: 21px;
    color: var(--brand-blue); text-align: center;
  }

  .tagline {
    font-family: "Oswald", "Arial Narrow", sans-serif;
    font-weight: 400; font-size: 19px; line-height: 40px;
    text-align: center;
  }
</style>
</head>
<body>
<main class="canvas">

  <section class="card card--front" aria-label="Business card front">
    <div class="card__panel card__panel--blue">
      <p class="person__name">Mark Holloway</p>
      <p class="person__role">Director</p>
      <div class="company">
        <p class="company__name">Kestrel Office Clearance</p>
        <p class="company__address">Unit K4 B,2-8 Fenwick Lane<br>Ashcombe,Northvale,ZZ9 4QT</p>
      </div>
      <ul class="contacts">
        <li class="contacts__item">
          <svg class="contacts__icon" viewBox="0 0 12 12"><path d="M3.5 0.5h5a1 1 0 0 1 1 1v9a1 1 0 0 1-1 1h-5a1 1 0 0 1-1-1v-9a1 1 0 0 1 1-1zM3.8 1.8v7.4h4.4V1.8zM6 9.7a0.6 0.6 0 1 0 0 1.2a0.6 0.6 0 1 0 0-1.2z" fill-rule="evenodd"/></svg>
          07700 153928
        </li>
        <li class="contacts__item">
          <svg class="contacts__icon" viewBox="0 0 12 12"><path d="M2.4 0.6l2 2.2-1 1.3c0.7 1.6 2 2.9 3.5 3.6l1.3-1 2.2 2-1.1 2.1C5 10.5 1.4 6.9 0.6 1.8z"/></svg>
          01632 960418
        </li>
        <li class="contacts__item">
          <svg class="contacts__icon" viewBox="0 0 12 12"><path d="M0.8 2.5h10.4v7H0.8zM1.4 3l4.6 3.6L10.6 3z" fill-rule="evenodd"/></svg>
          mark@kestrelofficeclearance.co.uk
        </li>
        <li class="contacts__item">
          <svg class="contacts__icon" viewBox="0 0 12 12"><circle cx="6" cy="6" r="5.4"/><path d="M3 4.2c1-0.3 1.6 0.4 1.3 1.2-0.4 0.9 0.6 1.4 0.4 2.4-0.2 0.9 0.5 1.6 1 2.4M7.6 1.4c-0.4 0.8 0.2 1.5 1 1.6 0.9 0.1 1 1 1.6 1.2" stroke="#0a7bc1" stroke-width="0.9" fill="none"/></svg>
          www.kestrelofficeclearance.co.uk
        </li>
      </ul>
    </div>
    <div class="card__panel card__panel--clear">
      <div class="brand-mark">
        <span class="brand-mark__dot"></span>
        <p class="brand-mark__name">Kestrel<br>Office Clearance</p>
      </div>
    </div>
  </section>

  <section class="card card--back" aria-label="Business card back">
    <div class="card__panel card__panel--clear">
      <div class="brand-mark">
        <span class="brand-mark__dot"></span>
        <p class="brand-mark__name">Kestrel<br>Office Clearance</p>
      </div>
    </div>
    <div class="card__panel card__panel--blue">
      <p class="tagline">tidy offices, zero fuss…<br>we handle every last desk.</p>
    </div>
  </section>

</main>
</body>
</html>
```